Business card por a urban DJ, up scale audience target

Need a sober design, modern, conservative colors but i can consider some options, y play rnb, hip hop, EDM and top40.

Business card for contact and personal info, double sided, use logo attrached please; im 42 so i need a card acording to my age an target audience.

Target Market(s)

Adult people, up scale audience

Industry/Entity Type

Music Download

Contact Information for Business Card

Cel (318) 4207265518 www.lumadrift.com

Requirements
Must have
• open mind
Nice to have
• open mind
Should not have
• DJ

```html
<!DOCTYPE html>
<html lang="en">
<head>
<meta charset="utf-8">
<title>Lumadrift Business Card</title>
<link href="https://fonts.googleapis.com/css2?family=Open+Sans:wght@400;700;800&display=swap" rel="stylesheet">
<style>
  :root {
    --ink: #2b2a29;
    --paper: #ffffff;
    --backdrop: #ece8e2;
  }
  * { margin: 0; padding: 0; box-sizing: border-box; }
  html, body { width: 1189px; height: 1200px; overflow: hidden; }
  body {
    background: var(--backdrop);
    font-family: "Open Sans", Arial, sans-serif;
    position: relative;
  }
  .card {
    position: absolute;
    left: 171px;
    width: 856px;
    height: 488px;
  }
  .card--front { top: 67px; background: var(--paper); }
  .card--back { top: 627px; background: var(--ink); }

  .brand-name {
    position: absolute;
    font-weight: 800;
    letter-spacing: 6px;
    text-align: center;
    line-height: 1;
  }
  .card--front .brand-name {
    left: 0; width: 856px; top: 110px;
    font-size: 96px;
    color: var(--ink);
  }
  .card--back .brand-name {
    left: 0; width: 856px; top: 170px;
    font-size: 104px;
    color: var(--paper);
  }

  .info-band {
    position: absolute;
    left: 0; top: 286px;
    width: 856px; height: 153px;
    background: var(--ink);
    color: var(--paper);
  }
  .identity {
    position: absolute;
    right: 455px; top: 28px;
    text-align: right;
  }
  .identity__name {
    font-size: 29px;
    font-weight: 700;
    letter-spacing: 0.5px;
    line-height: 36px;
  }
  .identity__address {
    font-size: 21px;
    line-height: 27px;
    margin-top: 4px;
  }
  .divider {
    position: absolute;
    left: 426px; top: 29px;
    width: 2px; height: 95px;
    background: var(--paper);
  }
  .contacts {
    position: absolute;
    left: 457px; top: 30px;
    list-style: none;
  }
  .contacts li {
    display: flex;
    align-items: center;
    height: 30px;
    font-size: 22px;
  }
  .contacts svg {
    width: 22px; height: 22px;
    margin-right: 11px;
    flex: none;
  }

  .back-url {
    position: absolute;
    left: 0; width: 856px; top: 418px;
    text-align: center;
    color: var(--paper);
    font-size: 22px;
  }
</style>
</head>
<body>
  <section class="card card--front">
    <div class="brand-name">LUMA</div>
    <div class="info-band">
      <div class="identity">
        <div class="identity__name">EMPLOYEE NAME</div>
        <div class="identity__address">P.O. Box 000, 4th Lane<br>Harbor Rise, New Zealand</div>
      </div>
      <div class="divider"></div>
      <ul class="contacts">
        <li>
          <svg viewBox="0 0 22 22" aria-hidden="true">
            <rect width="22" height="22" fill="#fff"/>
            <rect x="7" y="3" width="8" height="16" rx="1" fill="none" stroke="#2b2a29" stroke-width="1.6"/>
            <rect x="8.5" y="5" width="5" height="5" fill="#2b2a29"/>
          </svg>
          (318) 4207265518
        </li>
        <li>
          <svg viewBox="0 0 22 22" aria-hidden="true">
            <rect width="22" height="22" fill="#fff"/>
            <rect x="3" y="5" width="16" height="12" fill="none" stroke="#2b2a29" stroke-width="1.6"/>
            <path d="M3 5 L11 12 L19 5 M3 17 L9 11 M19 17 L13 11" fill="none" stroke="#2b2a29" stroke-width="1.4"/>
          </svg>
          hello@lumadrift.com
        </li>
        <li>
          <svg viewBox="0 0 22 22" aria-hidden="true">
            <rect width="22" height="22" fill="#fff"/>
            <circle cx="11" cy="11" r="7.5" fill="none" stroke="#2b2a29" stroke-width="1.5"/>
            <ellipse cx="11" cy="11" rx="3.5" ry="7.5" fill="none" stroke="#2b2a29" stroke-width="1.2"/>
            <path d="M3.5 11 H18.5 M5 7 H17 M5 15 H17" stroke="#2b2a29" stroke-width="1.2"/>
          </svg>
          www.lumadrift.com
        </li>
      </ul>
    </div>
  </section>

  <section class="card card--back">
    <div class="brand-name">LUMA</div>
    <div class="back-url">www.lumadrift.com</div>
  </section>
</body>
</html>
```